Structural Engineering Business Card

Brookvane Drafting does residential house plans for clients in Central Florida. Would like simple but elegant business card that is appropriate for a house plan engineering company. Prefer black business card with black/white them but open to other shades of blue. I uploaded a sample card that I came across that looked good but please come up with your own creative designs.

Contact Information for Business Card

Name, Title, Phone, Email, Address, website

```html
<!DOCTYPE html>
<html lang="en">
<head>
<meta charset="utf-8">
<title>Brookvane Drafting – Business Card</title>
<link rel="stylesheet" href="https://fonts.googleapis.com/css2?family=Poppins:wght@400;600;700&display=swap">
<style>
  :root {
    --page-bg: #e6e4e4;
    --card-front: #f2eeee;
    --card-back: #000000;
    --ink-dark: #0a0a0a;
    --ink-light: #ffffff;
    --gap: #ffffff;
  }
  * { margin: 0; padding: 0; box-sizing: border-box; }
  html, body {
    width: 1200px; height: 900px; overflow: hidden;
    background: var(--page-bg);
    font-family: "Poppins", sans-serif;
  }
  .card-spread {
    position: absolute; left: 55px; top: 113px;
    width: 1089px; height: 673px;
    display: flex; background: var(--gap);
  }
  .card-front {
    width: 508px; height: 100%;
    background: var(--card-front);
    display: flex; align-items: center; justify-content: center;
  }
  .brand-name {
    font-weight: 700; font-size: 40px; color: var(--ink-dark);
    letter-spacing: -0.5px; white-space: nowrap;
  }
  .card-back {
    margin-left: 21px; width: 560px; height: 100%;
    background: var(--card-back); color: var(--ink-light);
    padding: 180px 0 0 40px;
  }
  .person-name { font-weight: 600; font-size: 44px; line-height: 1.1; letter-spacing: 0.3px; }
  .person-title { font-size: 31px; line-height: 1.2; margin-bottom: 34px; }
  .contact-list { list-style: none; margin-bottom: 30px; }
  .contact-item {
    display: flex; align-items: center; gap: 14px;
    font-size: 31px; line-height: 40px;
  }
  .contact-icon { width: 30px; height: 30px; flex: none; }
  .address { font-size: 31px; line-height: 40px; }
</style>
</head>
<body>
  <div class="card-spread">
    <section class="card-front">
      <span class="brand-name">Brookvane Drafting</span>
    </section>
    <section class="card-back">
      <h1 class="person-name">DANIEL HARLOW</h1>
      <p class="person-title">Managing Director</p>
      <ul class="contact-list">
        <li class="contact-item">
          <svg class="contact-icon" viewBox="0 0 24 24" fill="none" stroke="currentColor" stroke-width="2"><path d="M5 3h4l2 5-2.5 1.5a11 11 0 0 0 6 6L16 13l5 2v4a2 2 0 0 1-2 2A16 16 0 0 1 3 5a2 2 0 0 1 2-2z"/></svg>
          407-555 0182
        </li>
        <li class="contact-item">
          <svg class="contact-icon" viewBox="0 0 24 24" fill="none" stroke="currentColor" stroke-width="2"><rect x="2" y="5" width="20" height="14"/><path d="M2 5l10 8 10-8M2 19l7-7M22 19l-7-7"/></svg>
          hello@brookvane.com
        </li>
        <li class="contact-item">
          <svg class="contact-icon" viewBox="0 0 24 24" fill="none" stroke="currentColor" stroke-width="1.8"><circle cx="12" cy="12" r="10"/><ellipse cx="12" cy="12" rx="4.5" ry="10"/><path d="M2 12h20M4 7h16M4 17h16"/></svg>
          www.brookvane.com
        </li>
      </ul>
      <p class="address">218, Cypress Hollow Lane<br>Orlando 32801, USA</p>
    </section>
  </div>
</body>
</html>
```